Good afternoon,
1. Can we also have the ‘Marblewren selections of the month’ moved to the left side and smaller than the logo quote ‘bright hearts at daybreak’ as it’s just a subheading. That said can we have the ‘Bright hearts at daybreak’ a little larger.
2. Can we have the order of the drop down menus as. Age then Theme then Location (no price). Next to these titles can we have a small image such as a locator point next to ‘location’, two people holding hands adult and child net to ‘age’ and something adventure/city next to ‘theme’, an image to represent the drop down menus. See below:

3. Can we please use this as a logo instead of what we have at the moment. And the same type of setup as what I have here. I really like this map of Australia. We have the rights to it and I have attached it as a file for you to use.

4. Can the selection buttons all be the same blue as the blue in the logo please. Can every part of the page have the logo blue/dirty orange also? Makes it calmer.

5. Could you please add a ‘calendar’ to the tabs (in blue at the top of the page, on the left of ‘add and activity’ .
Let me know how you go. Thanks

Target Market(s)

• Parents and care-givers
• Teachers
• Children (child-friendly)
• Customers are those who ask the question ‘what am I going to do with my child/ren this week/weekend/month’

Industry/Entity Type

Quote

Number of Pages Required

4 page

Font styles to use
Sans Serif

Requirements
Must have
• An ecommerce website (platform) with a responsive system for IOS and Android
• Easy to navigate, user-friendly clean
Nice to have
• some interactive maps
Should not have
• To much clutter/info

```html
<!DOCTYPE html>
<html lang="en">
<head>
<meta charset="utf-8">
<title>Marblewren Melbourne</title>
<link rel="stylesheet" href="https://fonts.googleapis.com/css2?family=Hind:wght@400;500;600&family=Open+Sans:wght@400;600&family=Roboto+Condensed:wght@700&display=swap">
<style>
:root{
  --orange:#f07246;
  --blue:#2f6fa6;
  --blue-deep:#255a88;
  --ink:#1e1e1e;
  --text:#444;
  --paper:#ffffff;
  --mist:#ececec;
  --footer:#282828;
  --footer-deep:#1b1b1b;
  --head:"Hind",sans-serif;
  --body:"Open Sans",sans-serif;
}
*{box-sizing:border-box;margin:0;padding:0}
html,body{width:1200px;height:3000px;overflow:hidden}
body{position:relative;background:var(--paper);font-family:var(--body);color:var(--text)}
.abs{position:absolute}

/* header */
.brand{left:60px;top:22px;font-family:var(--head);font-weight:600;font-size:46px;color:#5a5a5a;line-height:1;display:flex;align-items:center;gap:10px}
.brand-dot{width:16px;height:16px;border-radius:50%;background:var(--blue)}
.brand-city{left:246px;top:64px;font-family:var(--head);font-size:20px;color:var(--orange)}
.top-btn{top:36px;height:44px;background:var(--blue);color:#fff;font-family:var(--head);font-size:17px;display:flex;align-items:center;justify-content:center;border-radius:3px}

/* nav */
.nav{left:0;top:108px;width:1200px;height:44px;background:var(--orange)}
.nav-item{top:0;height:44px;line-height:46px;font-family:var(--head);font-weight:600;font-size:15px;color:#fff;letter-spacing:.3px;white-space:nowrap}
.nav-home{background:var(--ink);padding:0 10px;left:60px}
.nav-calendar{background:var(--blue);padding:0 14px}
.nav-search{left:1092px;top:0;width:48px;height:44px;background:var(--ink);display:flex;align-items:center;justify-content:center}

/* hero */
.hero{left:0;top:152px;width:1200px;height:558px;background:linear-gradient(180deg,#6f8f52 0%,#8fa86a 30%,#7c9aa8 62%,#5d7d8e 100%)}
.hero-caption{left:60px;top:170px;width:540px;background:rgba(25,25,25,.82);color:#fff;font-family:var(--head);font-weight:500;font-size:54px;line-height:60px;padding:24px 30px}

/* suggestions */
.band{left:0;top:710px;width:1200px;height:1096px;background:var(--mist)}
.finder{left:60px;top:50px;width:334px;height:432px;background:var(--orange);padding:34px 30px}
.finder h2{font-family:var(--head);font-weight:500;font-size:27px;line-height:34px;color:#fff}
.select{left:32px;width:262px;height:44px;background:#fff;border-radius:3px;font-size:15px;color:#777;display:flex;align-items:center;padding-left:12px;gap:10px}
.select svg{flex:none}
.select .caret{margin-left:auto;margin-right:16px;width:0;height:0;border-left:7px solid transparent;border-right:7px solid transparent;border-top:7px solid #999}
.finder-btn{left:32px;top:328px;width:258px;height:54px;background:var(--blue);color:#fff;font-family:var(--head);font-size:20px;display:flex;align-items:center;justify-content:center;border-radius:3px}
.section-bar{left:440px;top:50px;width:700px;height:54px;background:#fff}
.section-bar h2{position:absolute;left:14px;top:14px;font-family:var(--head);font-weight:500;font-size:22px;color:var(--ink)}
.arrow{width:36px;height:36px;background:var(--blue);display:flex;align-items:center;justify-content:center}
.card{background:#fff}
.card .photo{width:100%;height:222px}
.card h3{font-family:var(--head);font-weight:600;font-size:19px;line-height:22px;color:var(--ink);margin:22px 20px 12px}
.card p{font-size:13px;line-height:21px;color:#555;margin:0 20px}

/* themes */
.themes{left:0;top:1806px;width:1200px;height:534px;background:var(--orange)}
.themes h2{position:absolute;left:0;width:1200px;top:56px;text-align:center;font-family:var(--head);font-weight:500;font-size:44px;color:#fff}
.tile{top:168px}
.tile .photo{width:100%;height:212px;border:3px solid #fff}
.tile-label{position:absolute;top:238px;height:48px;background:#fff;font-family:var(--head);font-weight:500;font-size:19px;color:var(--blue-deep);display:flex;align-items:center;justify-content:center}
.tile-label::before{content:"";position:absolute;left:14px;top:-12px;border-left:12px solid transparent;border-right:12px solid transparent;border-bottom:12px solid #fff}

/* newsletter */
.news-title{left:0;width:1200px;top:2418px;text-align:center;font-family:"Roboto Condensed",sans-serif;font-weight:700;font-size:40px;color:var(--ink)}
.news-sub{left:0;width:1200px;top:2472px;text-align:center;font-size:14px;color:#333}
.news-input{left:376px;top:2532px;width:374px;height:38px;border:2px solid #ddd;font-size:13px;color:#888;padding-left:12px;line-height:34px}
.news-submit{left:750px;top:2532px;width:106px;height:38px;background:var(--blue);color:#fff;font-weight:600;font-size:15px;display:flex;align-items:center;justify-content:center}

/* footer */
.footer{left:0;top:2640px;width:1200px;height:316px;background:var(--footer);color:#fff}
.f-col{top:48px}
.f-col h4{font-family:var(--head);font-weight:500;font-size:25px;color:#fff}
.f-col h4::after{content:"";display:block;width:56px;height:4px;background:var(--orange);margin-top:6px}
.f-line{display:flex;align-items:center;gap:12px;font-size:14px;margin-top:16px}
.f-list{list-style:disc;margin:18px 0 0 20px;font-size:14px;line-height:23px}
.f-hours{margin-top:18px;font-size:14px;line-height:25px}
.social{display:flex;gap:8px;margin-top:30px}
.social span{width:28px;height:28px;border-radius:50%;border:2px solid #888;background:#555}
.map{left:870px;top:118px;width:256px;height:166px;background:linear-gradient(135deg,#e7e0cf,#cfd8c0 50%,#bcd0dc);border:2px solid #fff}
.copy{left:0;top:2956px;width:1200px;height:44px;background:var(--footer-deep);color:#bbb;font-size:13px;display:flex;align-items:center;justify-content:center}
</style>
</head>
<body>

<header>
  <div class="abs brand"><span class="brand-dot"></span>Marblewren</div>
  <div class="abs brand-city">Melbourne</div>
  <a class="abs top-btn" style="left:826px;width:160px">See our Suggestion</a>
  <a class="abs top-btn" style="left:998px;width:140px">Signup/Login</a>
</header>

<nav class="abs nav">
  <span class="abs nav-item nav-home">HOME</span>
  <span class="abs nav-item" style="left:150px">FOR WHOM?</span>
  <span class="abs nav-item" style="left:276px">LOCATION</span>
  <span class="abs nav-item" style="left:390px">PRICE</span>
  <span class="abs nav-item" style="left:470px">FEATURED ADVENTURES</span>
  <span class="abs nav-item nav-calendar" style="left:680px">CALENDAR</span>
  <span class="abs nav-item" style="left:812px">LIST AN ACTIVITY OR DESTINATION</span>
  <span class="abs nav-search">
    <svg width="24" height="24" viewBox="0 0 24 24"><circle cx="10" cy="10" r="7" fill="none" stroke="#fff" stroke-width="3"/><line x1="15" y1="15" x2="22" y2="22" stroke="#fff" stroke-width="3.5" stroke-linecap="round"/></svg>
  </span>
</nav>

<section class="abs hero" role="img" aria-label="Children in helmets and life jackets paddling a barrel raft on a lake">
  <div class="abs hero-caption">Bright hearts at daybreak</div>
</section>

<section class="abs band">
  <div class="abs finder">
    <h2>What to do with your children in Paris?</h2>
    <div class="abs select" style="top:138px">
      <svg width="22" height="18" viewBox="0 0 22 18"><circle cx="6" cy="3" r="2.6" fill="#2f6fa6"/><path d="M3 18V8a3 3 0 0 1 6 0v10z" fill="#2f6fa6"/><circle cx="17" cy="8" r="2" fill="#2f6fa6"/><path d="M14.5 18v-6a2.5 2.5 0 0 1 5 0v6z" fill="#2f6fa6"/><path d="M9 10.5h5.5" stroke="#2f6fa6" stroke-width="1.6"/></svg>Age<span class="caret"></span></div>
    <div class="abs select" style="top:194px">
      <svg width="22" height="18" viewBox="0 0 22 18"><path d="M0 18 7 6l4 6 3-4 8 10z" fill="#2f6fa6"/><rect x="15" y="1" width="3" height="7" fill="#2f6fa6"/><path d="M15 1h6l-2 2 2 2h-6" fill="#f07246"/></svg>Theme<span class="caret"></span></div>
    <div class="abs select" style="top:250px">
      <svg width="22" height="18" viewBox="0 0 22 18"><path d="M11 0a7 7 0 0 1 7 7c0 5-7 11-7 11S4 12 4 7a7 7 0 0 1 7-7z" fill="#2f6fa6"/><circle cx="11" cy="7" r="2.5" fill="#fff"/></svg>Location<span class="caret"></span></div>
    <div class="abs finder-btn">See your suggestion</div>
  </div>

  <div class="abs section-bar">
    <h2>Our suggestions this month</h2>
    <span class="abs arrow" style="left:612px;top:8px"><svg width="18" height="14" viewBox="0 0 18 14"><path d="M17 7H3M8 1 2 7l6 6" fill="none" stroke="#fff" stroke-width="2.5"/></svg></span>
    <span class="abs arrow" style="left:652px;top:8px"><svg width="18" height="14" viewBox="0 0 18 14"><path d="M1 7h14M10 1l6 6-6 6" fill="none" stroke="#fff" stroke-width="2.5"/></svg></span>
  </div>

  <article class="abs card" style="left:442px;top:122px;width:326px;height:426px">
    <div class="photo" role="img" aria-label="Children in helmets on a high ropes course in the trees" style="background:linear-gradient(180deg,#4f6f3a,#8aa56a)"></div>
    <h3>The Grand Palace of Mirrors</h3>
    <p>Lorem Ipsum has been the industry's standard dummy text ever since the 1500s, when an unknown printer took a galley of type and scrambled it to make a type specimen book. when an unknown printer took a galley of type and scrambled it to.</p>
  </article>
  <article class="abs card" style="left:812px;top:122px;width:326px;height:424px">
    <div class="photo" role="img" aria-label="Two girls running a trail race in the mountains" style="background:linear-gradient(180deg,#a9c7e0,#8fae6a 55%,#c8b79a)"></div>
    <h3>Concert of classical music and stories told</h3>
    <p>Lorem Ipsum has been the industry's standard dummy text ever since the 1500s, when an unknown printer took a galley of type and scrambled it to make a type specimen book.</p>
  </article>

  <article class="abs card" style="left:60px;top:596px;width:324px;height:424px">
    <div class="photo" role="img" aria-label="Two girls running a trail race in the mountains" style="background:linear-gradient(180deg,#a9c7e0,#8fae6a 55%,#c8b79a)"></div>
    <h3>Concert of classical music and stories told</h3>
    <p>Lorem Ipsum has been the industry's standard dummy text ever since the 1500s, when an unknown printer took a galley of type and scrambled it to make a type specimen book.</p>
  </article>
  <article class="abs card" style="left:442px;top:596px;width:326px;height:424px">
    <div class="photo" role="img" aria-label="Child with a ship's wheel and a toy treasure chest" style="background:linear-gradient(180deg,#e6ddd0,#c9a883 70%,#8a5a3a)"></div>
    <h3>Concert of classical music and stories told</h3>
    <p>Lorem Ipsum has been the industry's standard dummy text ever since the 1500s, when an unknown printer took a galley of type and scrambled it to make a type specimen book.</p>
  </article>
  <article class="abs card" style="left:812px;top:596px;width:326px;height:424px">
    <div class="photo" role="img" aria-label="Children playing with colourful puppets indoors" style="background:linear-gradient(135deg,#d9c6c9,#c65a7a 55%,#5a6fb0)"></div>
    <h3>Concert of classical music and stories told</h3>
    <p>Lorem Ipsum has been the industry's standard dummy text ever since the 1500s, when an unknown printer took a galley of type and scrambled it to make a type specimen book.</p>
  </article>
</section>

<section class="abs themes">
  <span class="abs arrow" style="left:1062px;top:26px"><svg width="18" height="14" viewBox="0 0 18 14"><path d="M17 7H3M8 1 2 7l6 6" fill="none" stroke="#fff" stroke-width="2.5"/></svg></span>
  <span class="abs arrow" style="left:1100px;top:26px"><svg width="18" height="14" viewBox="0 0 18 14"><path d="M1 7h14M10 1l6 6-6 6" fill="none" stroke="#fff" stroke-width="2.5"/></svg></span>
  <h2>Explore by theme</h2>

  <div class="abs tile" style="left:60px;width:228px">
    <div class="photo" role="img" aria-label="Modern building and spire against a blue sky" style="background:linear-gradient(180deg,#3f7fc4,#9cc3e4 60%,#555)"></div>
    <div class="tile-label" style="left:0;width:228px">Explore History</div>
  </div>
  <div class="abs tile" style="left:336px;width:236px">
    <div class="photo" role="img" aria-label="Visitor looking at a wall of framed posters" style="background:linear-gradient(135deg,#5a2a3a,#a33a3a 50%,#2f4f6a)"></div>
    <div class="tile-label" style="left:4px;width:228px">Explore History</div>
  </div>
  <div class="abs tile" style="left:620px;width:236px">
    <div class="photo" role="img" aria-label="Child walking through a gallery of framed paintings" style="background:linear-gradient(180deg,#4a3a2e,#7a5a3a 60%,#b98a55)"></div>
    <div class="tile-label" style="left:0;width:228px">Explore History</div>
  </div>
  <div class="abs tile" style="left:902px;width:236px">
    <div class="photo" role="img" aria-label="Path through a lush fern forest" style="background:linear-gradient(180deg,#2f4a28,#5f7a3e 60%,#6b5a3a)"></div>
    <div class="tile-label" style="left:6px;width:230px">Explore History</div>
  </div>
</section>

<section>
  <h2 class="abs news-title">Get Started With Our Newsletter</h2>
  <p class="abs news-sub">Free shipping, phenomenal customer service and wicked prices.</p>
  <div class="abs news-input">Enter your Email here</div>
  <div class="abs news-submit">Submit</div>
</section>

<footer class="abs footer">
  <div class="abs f-col" style="left:60px">
    <h4>Contact us</h4>
    <div class="f-line" style="margin-top:22px"><svg width="18" height="18" viewBox="0 0 18 18"><path d="M4 1l3 4-2 2c1 2.5 3.5 5 6 6l2-2 4 3-2 3C8 17 1 10 1 3z" fill="#fff"/></svg>9624118305</div>
    <div class="f-line"><svg width="18" height="14" viewBox="0 0 18 14"><rect x="1" y="1" width="16" height="12" fill="none" stroke="#fff" stroke-width="2"/><path d="M1 1l8 7 8-7" fill="none" stroke="#fff" stroke-width="2"/></svg>contact@marblewren.com.au</div>
    <div class="social"><span></span><span></span><span></span><span></span></div>
  </div>
  <div class="abs f-col" style="left:374px">
    <h4>Our Services</h4>
    <ul class="f-list"><li>Home</li><li>About Us</li><li>News</li><li>Free Tests</li><li>Fernly Stores</li><li>Community</li><li>Courses</li></ul>
  </div>
  <div class="abs f-col" style="left:628px">
    <h4>Store Hours</h4>
    <div class="f-hours">Monday:10am - 8pm<br>Tuesday:10am - 7pm<br>Wednesday:10am - 8pm<br>Thrusday: 10am - 8pm<br>Friday:10am - 8pm<br>Saturday:10am - 7pm</div>
  </div>
  <div class="abs f-col" style="left:870px">
    <h4>Our Location</h4>
  </div>
  <div class="abs map" role="img" aria-label="Street map of the city with the office marked"></div>
</footer>
<div class="abs copy">© 2016 Copyright Marblewren. All Right Reserved</div>

</body>
</html>
```